Mental Health care Company in Washington DC

We are a new mental health care services provider in Washington DC. Please look at these sites.
https://brightwaterfamilysupport.com
https://www.quietharborinc.com
https://willowgate-dc.org/
https://www.tidepathdc.com
https://www.thelanternofdc.com

```html
<!DOCTYPE html>
<html lang="en">
<head>
<meta charset="utf-8">
<title>Novaline Health Services – Mental Health Care in Washington DC</title>
<link href="https://fonts.googleapis.com/css2?family=Montserrat:wght@400;500;600;700;800&display=swap" rel="stylesheet">
<style>
:root{
  --navy:#132347;
  --teal:#a9dbe0;
  --teal-dark:#7cc3ca;
  --orange:#f2a05c;
  --grey-bg:#efefef;
  --text:#4a4f5c;
  --muted:#9aa0a8;
  --white:#ffffff;
}
*{box-sizing:border-box;margin:0;padding:0}
html,body{width:1200px;height:4464px;overflow:hidden}
body{font-family:'Montserrat',sans-serif;color:var(--navy);background:var(--white);position:relative}
.abs{position:absolute}
.btn{position:absolute;display:flex;align-items:center;justify-content:center;font-size:12px;font-weight:600;letter-spacing:.3px;color:var(--navy);background:var(--teal);border-radius:3px;text-transform:uppercase}
.btn.orange{background:var(--orange);color:var(--navy)}
.section-title{position:absolute;left:0;width:1200px;text-align:center;font-size:31px;font-weight:400;letter-spacing:.5px;text-transform:uppercase;color:var(--navy)}
.section-title b{font-weight:800}
p{line-height:1.6}

/* header */
.site-header{position:absolute;top:0;left:0;width:1200px;height:94px;background:var(--white);z-index:5}
.brand{position:absolute;left:142px;top:26px;display:flex;align-items:center;gap:10px}
.brand-dot{width:14px;height:14px;border-radius:50%;background:var(--teal)}
.brand-name{font-size:31px;font-weight:600;color:var(--navy);line-height:1}
.brand-sub{position:absolute;left:166px;top:62px;font-size:11px;letter-spacing:6px;color:var(--muted)}
.main-nav{position:absolute;right:140px;top:26px;display:flex;align-items:center;gap:46px;font-size:12px;font-weight:600}
.main-nav .btn{position:static;width:126px;height:42px}

/* hero */
.hero{position:absolute;top:94px;left:0;width:1200px;height:680px;overflow:hidden}
.hero-photo{position:absolute;inset:0;background:linear-gradient(180deg,#e9dccb 0%,#f1d7b0 35%,#c9a781 55%,#6f7a4e 78%,#3f4f2c 100%)}
.hero-copy{position:absolute;left:142px;top:100px}
.hero-copy .l1{font-size:34px;font-weight:400}
.hero-copy .l2{font-size:44px;font-weight:800;margin-top:4px}
.hero-copy .l3{font-size:33px;font-weight:400;margin-top:4px}
.hero-copy p{font-size:18px;line-height:1.45;margin-top:18px;color:var(--navy)}

/* about */
.about-photo{position:absolute;left:139px;top:832px;width:460px;height:460px;border-radius:60px;background:linear-gradient(135deg,#c9c1b3 0%,#e6e2dc 45%,#b8dde2 100%)}
.about-copy{position:absolute;left:666px;top:860px;width:400px}
.about-copy h2{font-size:31px;font-weight:400}
.about-copy h2 b{font-weight:800}
.about-copy .sub{font-size:20px;font-weight:600;color:#b9bec5;display:flex;align-items:center;gap:14px;margin-top:0}
.about-copy .sub span.rule{display:inline-block;width:90px;height:1px;background:#c6cbd1}
.about-copy p{font-size:12.5px;color:var(--text);margin-top:14px;line-height:1.75}

/* services */
.services{position:absolute;top:1387px;left:0;width:1200px;height:550px;background:var(--grey-bg)}
.card{position:absolute;top:151px;width:284px;height:305px;background:var(--white);border-radius:10px;box-shadow:0 8px 20px rgba(0,0,0,.06);text-align:center}
.card .icon{width:78px;height:78px;border-radius:50%;margin:32px auto 0;border:2px dashed;display:flex;align-items:center;justify-content:center}
.card .icon i{display:block;width:62px;height:62px;border-radius:50%}
.card h3{font-size:17px;font-weight:600;margin-top:26px}
.card p{font-size:12.5px;color:var(--text);padding:0 22px;margin-top:12px;line-height:1.75}

/* testimonials */
.avatar{position:absolute;border-radius:50%;background:linear-gradient(160deg,#d9d4cf,#8c8580)}
.quote{position:absolute;left:320px;top:2136px;width:560px;text-align:center;font-size:15px;font-style:italic;color:var(--text);line-height:1.6}
.stars{position:absolute;left:0;width:1200px;top:2096px;text-align:center;color:var(--orange);font-size:20px;letter-spacing:5px}
.client{position:absolute;left:0;width:1200px;text-align:center}

/* why */
.why{position:absolute;top:2459px;left:0;width:1200px;height:711px;background:var(--grey-bg)}
.feature h3{font-size:18px;font-weight:700}
.feature p{font-size:12.5px;color:var(--text);line-height:1.75;margin-top:6px}

/* contact */
.field{position:absolute;height:40px;border:1px solid #dcdfe3;border-radius:2px;background:var(--white);display:flex;align-items:center;font-size:11px;color:#555}
.field .ic{width:36px;height:100%;border-right:1px solid #e3e6ea;display:flex;align-items:center;justify-content:center;margin-right:10px}
.field .ic i{width:10px;height:10px;border-radius:50%;background:var(--orange)}

/* cta */
.cta{position:absolute;top:3728px;left:0;width:1200px;height:356px;background:linear-gradient(180deg,#9bb3c7 0%,#6f8aa0 35%,#33543f 62%,#4b6d85 80%,#2d4a62 100%)}

/* footer */
.site-footer{position:absolute;top:4084px;left:0;width:1200px;height:380px;background:var(--navy);color:var(--white)}
.site-footer h4{font-size:15px;font-weight:700;letter-spacing:.3px}
.site-footer li{list-style:none;font-size:12px;margin-bottom:14px}
.contact-item{display:flex;gap:12px;margin-bottom:18px;font-size:12px;line-height:1.5}
.contact-item b{font-weight:700}
.social{display:flex;align-items:center;gap:12px;font-size:12px;margin-bottom:14px}
.social i{width:28px;height:28px;border-radius:50%;border:1.5px solid var(--white)}
</style>
</head>
<body>

<header class="site-header">
  <div class="brand"><span class="brand-name">Novaline Health</span></div>
  <div class="brand-sub">SERVICES</div>
  <nav class="main-nav">
    <span>HOME</span><span>ABOUT US</span><span>SERVICES</span><span>OUR TEAM</span>
    <span class="btn">CONTACT US</span>
  </nav>
</header>

<section class="hero">
  <div class="hero-photo" role="img" aria-label="Runner on a mountain ridge at sunrise"></div>
  <div class="hero-copy">
    <div class="l1">Compassionate</div>
    <div class="l2">Mental Health Care</div>
    <div class="l3">in Washington DC</div>
    <p>Your journey to wellness begins with understanding.<br>We're here to guide you every step of the way.</p>
  </div>
  <div class="btn" style="left:142px;top:331px;width:205px;height:40px">Schedule Consultation</div>
  <svg class="abs" style="left:0;top:500px" width="1200" height="180" viewBox="0 0 1200 180">
    <path d="M0 110 C 160 220 420 150 640 80 C 820 22 950 20 1200 30 L1200 180 L0 180 Z" fill="#fff"/>
  </svg>
</section>
<svg class="abs" style="left:0;top:620px" width="1200" height="160" viewBox="0 0 1200 160">
  <path d="M180 112 C 330 170 520 150 720 80 C 850 34 940 20 1010 18 C 900 20 800 60 700 100 C 520 160 340 158 180 112 Z" fill="#f2a05c"/>
</svg>

<section class="about">
  <div class="about-photo" role="img" aria-label="Woman in a balanced yoga pose outdoors"></div>
  <div class="about-copy">
    <h2>ABOUT <b>NOVALINE HEALTH</b></h2>
    <div class="sub">SERVICES <span class="rule"></span></div>
    <p>Lorem ipsum dolor sit amet, consectetuer adipiscing elit sed diam nonummy nibh euismod tincidunt ut laoet dolo magna aliquam erat volutpat.</p>
    <p>Ut wisi enim ad minim veniam, quis nostrud exer ullamcorper suscipit lobortis nisl ut aliquip ex ea commodo consequat. Duis autem vel eum iriure dolor in hendrerit in vulputate velit esse molestie consequat, vel illum dolore eu feugilla facilisis at vero eros et accumsan et iusto odio dignissim qui blandit praesent luptatum zzril delenit augue duis dolore te feugait nulla facilisi. Lorem ipsum dolor sit amet, consectetuer adipiscing elit, sed diam nonummy.</p>
  </div>
  <div class="btn" style="left:667px;top:1217px;width:127px;height:40px">Read More</div>
</section>

<section class="services">
  <h2 class="section-title" style="top:84px">Our <b>Services</b></h2>
  <div class="card" style="left:142px"><div class="icon" style="border-color:var(--teal)"><i style="background:var(--teal)"></i></div><h3>Individual Therapy</h3><p>Ut wisi enim ad minim v quis nostrud exerci taton ullamcorper spit lobortis nisl ut aliquip ex ea comghmodo consequat. Duis autem vel eum iriure dolor in hendrerit in vulputa.</p></div>
  <div class="card" style="left:456px"><div class="icon" style="border-color:var(--orange)"><i style="background:var(--orange)"></i></div><h3>Group Therapy</h3><p>Ut wisi enim ad minim v quis nostrud exerci taton ullamcorper spit lobortis nisl ut aliquip ex ea comghmodo consequat. Duis autem vel eum iriure dolor in hendrerit in vulputa.</p></div>
  <div class="card" style="left:775px"><div class="icon" style="border-color:var(--teal)"><i style="background:var(--teal)"></i></div><h3>Psychiatric Services</h3><p>Ut wisi enim ad minim v quis nostrud exerci taton ullamcorper spit lobortis nisl ut aliquip ex ea comghmodo consequat. Duis autem vel eum iriure dolor in hendrerit in vulputa.</p></div>
</section>

<section class="testimonials">
  <h2 class="section-title" style="top:2022px">What Our <b>Clients Say</b></h2>
  <div class="avatar" style="left:229px;top:2016px;width:96px;height:96px" role="img" aria-label="Client portrait"></div>
  <div class="avatar" style="left:123px;top:2166px;width:66px;height:66px" role="img" aria-label="Client portrait"></div>
  <div class="avatar" style="left:250px;top:2285px;width:80px;height:80px" role="img" aria-label="Client portrait"></div>
  <div class="avatar" style="left:983px;top:2039px;width:114px;height:114px" role="img" aria-label="Client portrait"></div>
  <div class="avatar" style="left:897px;top:2225px;width:100px;height:100px" role="img" aria-label="Client portrait"></div>
  <div class="stars">★★★★★</div>
  <p class="quote">"Lorem ipsum dolor sit amet, consectetuer adipiscing elit, sed diam nonummy nibh euismod tincidunt ut laoreet dolore magna aliquam erat volutpat. Ut wisi enim ad minim veniam, quis nostrud exerci tation ullamcorper suscipit lobortis nisl ut aliquip ex ea commodo consequat. Duis autem vel eum iriure dolor in hendrerit in vulputate velit."</p>
  <div class="client" style="top:2274px;font-size:15px;font-weight:700;letter-spacing:.5px">DANA &amp; LEE K.</div>
  <div class="client" style="top:2302px;font-size:13px;color:var(--text)">Austin, TX</div>
  <svg class="abs" style="left:570px;top:2332px" width="60" height="14"><circle cx="10" cy="7" r="4.5" fill="none" stroke="#888"/><circle cx="30" cy="7" r="4.5" fill="#a9dbe0"/><circle cx="50" cy="7" r="4.5" fill="none" stroke="#888"/></svg>
</section>

<section class="why">
  <h2 class="section-title" style="top:85px">Why <b>Choose Us</b></h2>
  <svg class="abs" style="left:380px;top:140px" width="440" height="420" viewBox="0 0 440 420">
    <circle cx="220" cy="207" r="192" fill="#fff"/>
    <path d="M110 52 A192 192 0 0 0 137 380" fill="none" stroke="#a9dbe0" stroke-width="2"/>
    <path d="M300 33 A192 192 0 0 1 300 380" fill="none" stroke="#f2a05c" stroke-width="2"/>
    <path d="M110 52 A192 192 0 0 1 300 33" fill="none" stroke="#a9dbe0" stroke-width="2"/>
    <circle cx="110" cy="52" r="5" fill="#fff" stroke="#a9dbe0"/>
    <circle cx="410" cy="175" r="5" fill="#fff" stroke="#f2a05c"/>
    <circle cx="137" cy="378" r="5" fill="#fff" stroke="#a9dbe0"/>
    <circle cx="220" cy="207" r="80" fill="#f6f7f8"/>
  </svg>
  <!-- feature icon badges -->
  <svg class="abs" style="left:370px;top:180px" width="130" height="130"><path d="M20 65 A50 50 0 0 1 110 40" fill="none" stroke="#a9dbe0" stroke-width="18"/><circle cx="63" cy="65" r="48" fill="#fff"/><rect x="48" y="50" width="26" height="30" rx="2" fill="none" stroke="#132347" stroke-width="2"/><circle cx="76" cy="76" r="9" fill="#fff" stroke="#132347" stroke-width="2"/><path d="M76 71v5h4" stroke="#132347" stroke-width="2" fill="none"/></svg>
  <svg class="abs" style="left:700px;top:180px" width="130" height="130"><path d="M20 65 A50 50 0 0 1 110 40" fill="none" stroke="#a9dbe0" stroke-width="18"/><circle cx="67" cy="65" r="48" fill="#fff"/><circle cx="67" cy="55" r="10" fill="none" stroke="#132347" stroke-width="2"/><path d="M50 84 C50 70 84 70 84 84" fill="none" stroke="#132347" stroke-width="2"/></svg>
  <svg class="abs" style="left:535px;top:460px" width="130" height="130"><path d="M12 70 A53 53 0 0 1 118 70" fill="none" stroke="#f2a05c" stroke-width="18"/><circle cx="65" cy="65" r="48" fill="#fff"/><circle cx="65" cy="65" r="20" fill="none" stroke="#132347" stroke-width="2"/><circle cx="65" cy="60" r="6" fill="none" stroke="#132347" stroke-width="2"/><path d="M55 76 C57 68 73 68 75 76" fill="none" stroke="#132347" stroke-width="2"/></svg>
  <div class="feature abs" style="left:110px;top:203px;width:253px;text-align:right"><h3>Flexible Scheduling</h3><p>We offer evening and weekend appointments to accommodate your busy lifestyle.</p></div>
  <div class="feature abs" style="left:832px;top:203px;width:260px"><h3>Experienced Therapists</h3><p>Our team consists of licensed professionals with years of experience in various mental health specialties.</p></div>
  <div class="feature abs" style="left:668px;top:540px;width:250px"><h3>Personalized Approach</h3><p>We develop individualized treatment plans tailored to your unique needs and circumstances.</p></div>
</section>

<section class="contact">
  <h2 class="section-title" style="top:3256px">Get In <b>Touch</b></h2>
  <p class="abs" style="left:370px;top:3308px;width:460px;text-align:center;font-size:13px;color:var(--text)">Lorem ipsum dolor sit amet, consectetuer adipiscing elit sed diam nonummy nibh euismod tincidunt.</p>
  <div class="field" style="left:303px;top:3369px;width:289px"><span class="ic"><i></i></span>First Name*</div>
  <div class="field" style="left:607px;top:3369px;width:289px"><span class="ic"><i></i></span>Last Name*</div>
  <div class="field" style="left:303px;top:3424px;width:289px"><span class="ic"><i></i></span>Your Phone*</div>
  <div class="field" style="left:607px;top:3424px;width:289px"><span class="ic"><i></i></span>Your Email*</div>
  <div class="field" style="left:303px;top:3480px;width:593px;height:84px;align-items:flex-start"><span class="ic" style="height:40px"><i></i></span><span style="margin-top:13px">Your Message</span></div>
  <div class="btn" style="left:536px;top:3593px;width:126px;height:41px">Submit Now</div>
</section>

<section class="cta" role="img" aria-label="Person meditating on a lakeside dock with forested hills">
  <h2 class="abs" style="left:0;top:74px;width:1200px;text-align:center;color:#fff;font-size:27px;font-weight:400">READY TO START YOUR <b style="font-weight:800">JOURNEY TO WELLNESS?</b></h2>
  <p class="abs" style="left:0;top:116px;width:1200px;text-align:center;color:#fff;font-size:21px">Schedule a consultation with one of our experienced therapists today.</p>
  <div class="btn orange" style="left:497px;top:170px;width:206px;height:42px">Schedule Consultation</div>
</section>

<footer class="site-footer">
  <div class="abs" style="left:142px;top:55px">
    <h4>QUICK LINKS</h4>
    <ul style="margin-top:30px"><li>• Home</li><li>• About Us</li><li>• Services</li><li>• Our Team</li><li>• Contact Us</li></ul>
  </div>
  <div class="abs" style="left:369px;top:55px;width:240px">
    <h4>CONTACT DETAILS</h4>
    <div style="margin-top:30px">
      <div class="contact-item"><svg width="12" height="16"><path d="M6 1a5 5 0 0 1 5 5c0 4-5 9-5 9S1 10 1 6a5 5 0 0 1 5-5z" fill="#fff"/><circle cx="6" cy="6" r="2" fill="#132347"/></svg><div><b>ADDRESS</b><br>123 Ut Wisi Enim Ad Minim<br>Veniam Quis, California.</div></div>
      <div class="contact-item"><svg width="12" height="14"><path d="M2 1l3 0 1 3-2 1c1 2 2 3 4 4l1-2 3 1v3c-6 0-10-4-10-10z" fill="#fff"/></svg><div><b>PHONE</b><br>123 456 7890</div></div>
      <div class="contact-item"><svg width="12" height="12"><rect x="0" y="2" width="12" height="8" fill="#fff"/><path d="M0 2l6 5 6-5" stroke="#132347" fill="none"/></svg><div><b>EMAIL</b><br>info@novalinehealth.com</div></div>
    </div>
  </div>
  <div class="abs" style="left:673px;top:55px">
    <h4>FOLLOW US</h4>
    <div style="margin-top:26px">
      <div class="social"><i></i>Community Page</div>
      <div class="social"><i></i>Video Channel</div>
      <div class="social"><i></i>Photo Journal</div>
      <div class="social"><i></i>Short Updates</div>
    </div>
  </div>
  <div class="abs" style="left:142px;top:329px;width:916px;height:1px;background:rgba(255,255,255,.15)"></div>
  <p class="abs" style="left:0;top:346px;width:1200px;text-align:center;font-size:12px">© 2025 Novaline Health Services. All Rights Reserved.</p>
</footer>

</body>
</html>
```